Telecommunications/Power civil contractor needs business card design

Were a new telecommunications/power underground civil contractor that is looking for a new business card design. Our company colours are silver or grey and orange. Feel free to use the white background logo or the black background logo.

Target Market(s)

Local contractors, utility companies, private sector mining/energy companies, developers.

Industry/Entity Type

Telecommunications

Contact Information for Business Card

Each card will need the following info:
Persons name:
Title:
E-mail:
Phone number:
Shop Address:
Mailing Address:

Requirements
Must have
• Each card will need the following info:
• Persons name:
• Title:
• E-mail:
• Phone number:
• Shop Address:
• Mailing Address:

```html
<!DOCTYPE html>
<html lang="en">
<head>
<meta charset="utf-8">
<title>Ridgeline Civil Works Inc — Business Card</title>
<link rel="stylesheet" href="https://fonts.googleapis.com/css2?family=Open+Sans:wght@400;700&display=swap">
<style>
  :root {
    --backdrop: #2b2b2d;
    --card: #0c0c0d;
    --card-back: #111113;
    --orange: #f2631c;
    --silver: #8e8f93;
    --text-grey: #9a9a9e;
  }
  * { box-sizing: border-box; margin: 0; padding: 0; }
  html, body {
    width: 1200px; height: 716px; overflow: hidden;
    background: var(--backdrop);
    font-family: "Open Sans", Arial, sans-serif;
  }
  .canvas {
    position: relative; width: 1200px; height: 716px;
    display: flex; align-items: center; justify-content: center; gap: 60px;
  }
  .card {
    position: relative; width: 500px; height: 286px;
    background: var(--card);
    border-radius: 3px;
    box-shadow: 0 18px 40px rgba(0,0,0,.55);
  }
  /* front */
  .card-front { display: flex; align-items: center; padding: 0 40px; }
  .brand-block {
    width: 175px; display: flex; flex-direction: column; align-items: center;
    gap: 12px; margin-top: -30px;
  }
  .brand-dot {
    width: 40px; height: 40px; border-radius: 50%;
    border: 3px solid var(--orange);
  }
  .brand-name {
    color: var(--orange); font-weight: 700; font-size: 15px;
    text-align: center; line-height: 1.25; letter-spacing: .5px;
    text-transform: uppercase;
  }
  .contact-block { flex: 1; padding-left: 20px; margin-top: -10px; }
  .person-name { color: var(--orange); font-weight: 700; font-size: 14px; }
  .person-title { color: var(--text-grey); font-size: 13px; margin-top: 2px; }
  .divider { height: 1px; background: var(--orange); margin: 14px 0 14px; }
  .address { color: var(--text-grey); font-size: 12.5px; line-height: 1.5; margin-bottom: 8px; }
  .contact-line {
    display: flex; align-items: center; gap: 8px;
    color: var(--text-grey); font-size: 12.5px; line-height: 1.7;
  }
  .contact-line svg { width: 12px; height: 12px; fill: var(--orange); flex: none; }
  /* back */
  .card-back {
    background: var(--card-back);
    display: flex; flex-direction: column; align-items: center; justify-content: center; gap: 16px;
  }
  .card-back .brand-dot { width: 64px; height: 64px; border-width: 4px; }
  .card-back .brand-name { font-size: 24px; }
</style>
</head>
<body>
<main class="canvas">
  <section class="card card-front" aria-label="Card front">
    <div class="brand-block">
      <span class="brand-dot" aria-hidden="true"></span>
      <p class="brand-name">Ridgeline<br>Civil Works Inc</p>
    </div>
    <div class="contact-block">
      <p class="person-name">Corin Ashby</p>
      <p class="person-title">Managing Director</p>
      <div class="divider"></div>
      <p class="address">N. 1 Sample Road,<br>Suite 100, Lakeview, WA 55555</p>
      <p class="contact-line">
        <svg viewBox="0 0 24 24" aria-hidden="true"><path d="M6.6 10.8a15.1 15.1 0 0 0 6.6 6.6l2.2-2.2a1 1 0 0 1 1-.25 11.4 11.4 0 0 0 3.6.57 1 1 0 0 1 1 1V20a1 1 0 0 1-1 1A17 17 0 0 1 3 4a1 1 0 0 1 1-1h3.5a1 1 0 0 1 1 1c0 1.25.2 2.45.57 3.57a1 1 0 0 1-.25 1z"/></svg>
        555 010 234
      </p>
      <p class="contact-line">
        <svg viewBox="0 0 24 24" aria-hidden="true"><path d="M2 5h20v14H2zm2 2v.5l8 5 8-5V7zm0 2.8V17h16V9.8l-8 5z"/></svg>
        info@ridgelinecivilinc.com
      </p>
    </div>
  </section>
  <section class="card card-back" aria-label="Card back">
    <span class="brand-dot" aria-hidden="true"></span>
    <p class="brand-name">Ridgeline<br>Civil Works Inc</p>
  </section>
</main>
</body>
</html>
```